ClinicNook Magazine Design for a digital monthly magazine

Designing an online magazine for monthly distribution. The magazine will be related to topics that are important to physicians. Finance, family, self-employment, medications, supplies, residency, continuing education, trends, advances, technology, etc. An example of another company that writes a monthly medical digital magazine editorial is Tavrin Health Digest. Here is a link to one of their editions. https://pagefold.example/tavrinhealthdigest/docs/tav_april2021?fr=kQ7wLpZx2Rm9Vt I want our project to be more modern looking, less busy, and much more friendly to the eye. We have a website design project in process through SketchHive currently. I've spliced together some of our favorite parts of the designs that were submitted so far so you can have a vision for the theme, colors, and logos.
I’m looking for a template for the cover and inside page layout.

Target Market(s)

Physicians

Industry/Entity Type

Medical

Font styles to use
Other font styles liked:
• Rubik

Colors
0054AA
0677BA
7BADD7
CADEEF
E8F1F8
59FF00
82FF00
B8FF75
E3FFCB
F4FFEA

Requirements
Must have
• Project must be centered around Physicians. Discusses topics that are physician centric. Finance, family, medical supplies, insurance, billing, technology, private practice, employed practice, etc.
Nice to have
• The ability to create a 15 - 20 page monthly editorial from the design theme and structure that you create
Should not have
• should not bee to busy and flat looking. Must be modern and welcoming to the eye

```html
<!DOCTYPE html>
<html lang="en">
<head>
<meta charset="utf-8">
<title>ClinicNook Magazine – Cover and Inside Pages</title>
<link rel="stylesheet" href="https://fonts.googleapis.com/css2?family=Fira+Sans:wght@300;400;600;700;800&family=Fira+Sans+Condensed:wght@700;800&display=swap">
<style>
:root{
  --blue:#3f60aa;
  --blue-deep:#2f4f97;
  --green:#8cc63f;
  --teal:#6db8a3;
  --ink:#2c2c2c;
  --grey-text:#8a8a8a;
  --paper:#f1f1f1;
  --paper-2:#fafafa;
  --canvas:#ffffff;
  --sans:'Fira Sans',sans-serif;
  --cond:'Fira Sans Condensed',sans-serif;
}
*{box-sizing:border-box;margin:0;padding:0}
html,body{width:1200px;height:1200px;overflow:hidden;background:var(--canvas);font-family:var(--sans);color:var(--ink)}
.sheet{position:absolute;overflow:hidden;box-shadow:0 10px 22px rgba(0,0,0,.16)}
.abs{position:absolute}
.photo{position:absolute}
.body-copy{position:absolute;font-size:4.2px;line-height:6.4px;color:var(--grey-text);text-align:justify}
.body-copy b{color:var(--ink);font-weight:700;display:block;font-size:4.4px}
.kicker{display:block;font-size:3.8px;color:var(--grey-text);text-transform:uppercase}

/* ---------- cover ---------- */
.cover{left:120px;top:110px;width:365px;height:530px;background:var(--blue)}
.cover-bar{position:absolute;left:0;top:0;width:100%;height:42px;display:flex;align-items:center;padding:0 28px 0 52px;color:#fff}
.brand{display:flex;align-items:center;gap:5px;font-weight:600;font-size:7px;letter-spacing:.3px}
.brand-dot{width:12px;height:12px;border-radius:50%;border:1.4px solid #fff}
.issue-meta{margin-left:auto;display:flex;gap:10px;font-size:5px}
.issue-meta span{border-bottom:.6px solid #fff;padding-bottom:1px}
.issue-meta strong{font-weight:700}
.cover-photo{left:0;top:42px;width:100%;height:318px;background:linear-gradient(120deg,#dfe8ef 0%,#f4f6f7 40%,#e9e4df 75%,#cfd9e2 100%)}
.cover-mag{position:absolute;right:-20px;top:352px;font-size:110px;font-weight:800;color:rgba(255,255,255,.08);transform:rotate(90deg);transform-origin:center;line-height:1;width:150px}
.cover-title{position:absolute;left:16px;top:382px;color:#fff}
.cover-title .thin{font-weight:300;font-size:21px;line-height:22px}
.cover-title .bold{font-weight:700;font-size:29px;line-height:28px;letter-spacing:.3px}
.cover-title .accent{font-weight:600;font-size:21px;line-height:22px;color:var(--teal)}
.cover-deck{position:absolute;left:19px;top:459px;width:160px;font-size:5.4px;line-height:9px;color:rgba(255,255,255,.55);text-transform:uppercase;font-weight:300}
.cover-deck strong{color:#fff;font-weight:700}
.cover-rule{position:absolute;left:55px;top:495px;width:215px;border-top:.8px dotted rgba(255,255,255,.5)}

/* ---------- spread ---------- */
.spread{display:flex}
.page{position:relative;height:100%;width:50%;background:var(--paper)}
.page.right{background:var(--paper-2)}
.folio{position:absolute;top:14px;font-size:5px;font-weight:600}
.running{position:absolute;top:12px;font-size:5.5px;color:#555}
.folio-line{position:absolute;top:17px;border-top:.5px dotted #999}

/* contents + editor */
.contents{left:580px;top:198px;width:470px;height:342px}
.toc-thumb{left:20px;width:64px;height:44px;background:linear-gradient(135deg,#a7c4d9,#e5eef4 60%,#9db5c6)}
.toc-num{position:absolute;left:24px;font-size:34px;font-weight:800;color:rgba(255,255,255,.75);line-height:1}
.toc-list{position:absolute;left:94px;width:140px}
.toc-item{display:flex;gap:4px;font-size:4px;line-height:6px;color:var(--grey-text);text-transform:uppercase;border-bottom:.5px dotted #888;padding-bottom:3px;margin-bottom:8px}
.toc-item .pg{font-size:6px;font-weight:700;color:var(--ink);white-space:nowrap}
.toc-item b{color:var(--ink)}
.toc-band{position:absolute;left:6px;top:164px;width:229px;height:7px;background:var(--green)}
.toc-head{position:absolute;left:56px;top:154px;font-family:var(--cond);font-weight:800;font-size:25px;color:var(--ink);letter-spacing:.5px}
.editor{background:var(--blue)}
.editor-photo{right:11px;top:9px;width:100px;height:100px;border-radius:50%;background:radial-gradient(circle at 55% 45%,#f1ece8 0 30%,#d9dfe6 60%,#b9c7d6)}
.editor-badge{left:82px;top:30px;width:60px;height:60px;border-radius:50%;background:var(--teal);display:flex;align-items:center;justify-content:center;text-align:center;color:#fff;font-size:3.6px;font-weight:700;line-height:4.6px;padding:0 8px}
.editor-title{position:absolute;left:25px;top:100px;color:#fff}
.editor-title .thin{font-weight:300;font-size:18px}
.editor-title .bold{font-weight:600;font-size:25px;margin-left:20px;line-height:22px}
.editor-rule{left:30px;top:157px;width:180px;border-top:.6px dotted rgba(255,255,255,.5)}
.quote-mark{position:absolute;font-family:var(--sans);font-weight:800;font-size:26px;color:#fff;line-height:1}
.editor-copy{left:74px;top:170px;width:80px;font-size:3.7px;line-height:6.2px;color:rgba(255,255,255,.85);font-style:italic}

/* supplies */
.supplies{left:110px;top:705px;width:470px;height:340px}
.captions{position:absolute;left:100px;top:38px;font-size:3.8px;line-height:6px;color:var(--grey-text);text-transform:uppercase}
.captions b{color:var(--ink)}
.section-title{position:absolute;font-weight:300;font-size:17px;color:#555;line-height:17px}
.section-title .accent{display:block;font-weight:600;font-size:22px;color:var(--teal);margin-left:22px;line-height:22px}
.photo.heart{left:50px;top:150px;width:42px;height:42px;background:linear-gradient(135deg,#eee,#d5d5d5 60%,#d44 61%,#c33 70%,#e8e8e8 71%)}
.photo.desk{left:100px;top:133px;width:126px;height:86px;background:linear-gradient(90deg,#eef0f2,#dfe5ea 50%,#f3f3f3)}
.photo.nurse{left:0;top:0;width:107px;height:340px;background:linear-gradient(180deg,#e7e0d8 0%,#e9d5c8 35%,#4fbfbd 60%,#37aab0 100%)}
.pull{left:80px;top:222px;width:125px;height:88px;background:var(--green);padding:12px 10px 0 36px;font-family:var(--sans);font-weight:800;font-size:9.5px;line-height:10.5px;color:#1d2a12;text-transform:uppercase;clip-path:polygon(0 0,96% 0,100% 5%,100% 100%,4% 100%,0 95%)}
.pull-mark{left:80px;top:203px;color:var(--green)}
.side-running{position:absolute;right:8px;font-size:5.5px;color:#555;transform:rotate(90deg);transform-origin:right top}

/* employment */
.employment{left:620px;top:705px;width:465px;height:340px}
.photo.surgeon{left:20px;top:38px;width:124px;height:186px;background:linear-gradient(180deg,#e9ecef 0%,#b9cde3 30%,#7fa4d0 60%,#6f93c2 100%)}
.photo.paper{left:151px;top:158px;width:72px;height:52px;background:linear-gradient(135deg,#f6f6f6,#dfe6ee)}
.photo.blocks{left:82px;top:90px;width:76px;height:100px;background:linear-gradient(160deg,#f4f4f4 0 35%,#d8b58c 36%,#c89e6e 100%)}
.photo.pink{left:10px;top:250px;width:70px;height:56px;background:linear-gradient(135deg,#f1c8cd,#e9b2bb)}
.banner{position:absolute;left:134px;top:219px;width:196px;height:22px;background:var(--green);padding:4px 6px;font-size:3.7px;line-height:5.2px;font-weight:700;color:#fff;text-transform:uppercase}
.caption-box{left:20px;top:295px;width:204px;height:34px;background:var(--blue);padding:6px 6px;font-size:3.6px;line-height:5.6px;color:rgba(255,255,255,.75);text-transform:uppercase}
.caption-box b{color:#fff}
</style>
</head>
<body>

<!-- ===== Cover ===== -->
<section class="sheet cover" aria-label="Magazine cover">
  <header class="cover-bar">
    <div class="brand"><span class="brand-dot"></span>CLINICNOOK</div>
    <div class="issue-meta"><span>APRIL 2020</span><strong>ISSUE #53</strong><span>RECOMENDED PRICE 9.99$</span></div>
  </header>
  <div class="photo cover-photo" role="img" aria-label="Smiling physician in a white coat with stethoscope, seated at a desk beside an anatomy model"></div>
  <div class="cover-mag">mag</div>
  <h1 class="cover-title">
    <div class="thin">SMART</div>
    <div class="bold">PHYSICIAN</div>
    <div class="accent">FINANCE</div>
  </h1>
  <p class="cover-deck"><strong>Explain to you how all</strong> this mistaken idea of denouncing pleasure and praising pain was born and I will give you a complete account of the</p>
  <div class="cover-rule"></div>
</section>

<!-- ===== Contents + Editor letter ===== -->
<section class="sheet spread contents" aria-label="Contents and editor letter spread">
  <div class="page">
    <div class="photo toc-thumb" style="top:48px" role="img" aria-label="Doctor consulting a patient"></div>
    <div class="toc-num" style="top:50px">22</div>
    <p class="body-copy" style="left:20px;top:96px;width:66px"><b>EXPLAIN TO YOU HOW ALL</b>Doctors plan savings early, track practice costs and build steady habits for family, billing and long careers ahead.</p>
    <div class="toc-list" style="top:48px">
      <div class="toc-item"><span class="pg">PAGE 02</span><span><b>Explain to you how all</b> this mistaken idea of denouncing pleasure and praising pain</span></div>
      <div class="toc-item"><span class="pg">PAGE 04</span><span><b>Explain to you how all</b> this mistaken idea of denouncing pleasure and praising pain</span></div>
      <div class="toc-item"><span class="pg">PAGE 06</span><span><b>Explain to you how all</b> this mistaken idea of denouncing pleasure and praising pain</span></div>
      <div class="toc-item"><span class="pg">PAGE 08</span><span><b>Explain to you how all</b> this mistaken idea of denouncing pleasure and praising pain</span></div>
    </div>
    <div class="toc-band"></div>
    <h2 class="toc-head">CONTENT</h2>
    <div class="photo toc-thumb" style="top:195px" role="img" aria-label="Stethoscope and medical tools"></div>
    <div class="toc-num" style="top:197px">24</div>
    <p class="body-copy" style="left:20px;top:243px;width:66px"><b>EXPLAIN TO YOU HOW ALL</b>Doctors plan savings early, track practice costs and build steady habits for family, billing and long careers ahead.</p>
    <div class="toc-list" style="top:195px">
      <div class="toc-item"><span class="pg">PAGE 13</span><span><b>Explain to you how all</b> this mistaken idea of denouncing pleasure and praising pain</span></div>
      <div class="toc-item"><span class="pg">PAGE 15</span><span><b>Explain to you how all</b> this mistaken idea of denouncing pleasure and praising pain</span></div>
      <div class="toc-item"><span class="pg">PAGE 17</span><span><b>Explain to you how all</b> this mistaken idea of denouncing pleasure and praising pain</span></div>
      <div class="toc-item"><span class="pg">PAGE 19</span><span><b>Explain to you how all</b> this mistaken idea of denouncing pleasure and praising pain</span></div>
    </div>
  </div>
  <div class="page editor">
    <div class="photo editor-photo" role="img" aria-label="Portrait of the editor, a physician in a white coat"></div>
    <div class="abs editor-badge">CLINICNOOK ON PHYSICIAN FINANCE</div>
    <h2 class="editor-title"><div class="thin">Welcome</div><div class="bold">editor letter</div></h2>
    <div class="abs editor-rule"></div>
    <span class="quote-mark" style="left:48px;top:166px">“</span>
    <p class="abs editor-copy">Welcome to this month's issue. We gathered practical ideas on saving, investing and planning so every physician can protect time with family. Inside you will find guidance on private practice, billing, insurance and new technology shaping daily clinical work. Our writers spoke with advisors, residents and senior doctors to share honest lessons. Read slowly, keep what helps, and share your own stories with our team for future issues. Thank you for reading along with us.</p>
    <span class="quote-mark" style="left:178px;top:300px">”</span>
  </div>
</section>

<!-- ===== Medical supplies ===== -->
<section class="sheet spread supplies" aria-label="Medical supplies spread">
  <div class="page">
    <span class="folio" style="left:18px">04</span>
    <div class="folio-line" style="left:30px;width:150px"></div>
    <span class="running" style="right:10px">runningTitle</span>
    <div class="captions"><b>PHOTO1.</b> Nemo enim ipsam voluptatem quia voluptas<br><b>PHOTO2.</b> Enim ad minima veniam, quis nostrum exercitationem<br><b>PHOTO3.</b> Minus id quod maxime placeat facere possimus</div>
    <h2 class="section-title" style="left:20px;top:93px">medical<span class="accent">supplies</span></h2>
    <div class="photo heart" role="img" aria-label="Stethoscope beside a red heart model"></div>
    <div class="photo desk" role="img" aria-label="Physician working at a desk with a computer"></div>
    <p class="body-copy" style="left:20px;top:200px;width:74px">Clinics that review supply orders each quarter often cut waste, keep shelves ready and free budget for staff training.</p>
    <p class="body-copy" style="left:100px;top:225px;width:126px">Simple inventory lists, shared with nurses, help teams spot shortages early and avoid rushed purchases at higher prices.</p>
    <p class="body-copy" style="left:20px;top:272px;width:74px"><span class="kicker">Sed ut perspiciatis</span><b>UNDE OMNIS ISTE NATUS ONSEQUATUR</b>Compare vendors yearly, ask peers for references and track delivery times before signing long contracts.</p>
    <p class="body-copy" style="left:100px;top:262px;width:126px"><span class="kicker">Nemo enim ipsam</span><b>VOLUPTATEM QUIA VOLUPTAS</b>Group purchasing can lower costs for small practices. Agree on standard items, review usage together and keep simple records for every order placed.</p>
  </div>
  <div class="page right">
    <div class="photo nurse" role="img" aria-label="Young nurse in teal scrubs with a stethoscope, arms crossed"></div>
    <span class="quote-mark pull-mark">“</span>
    <div class="abs pull">Connect with your physician peers and physician advisors to help you</div>
    <p class="body-copy" style="left:118px;top:40px;width:80px"><span class="kicker">Nemo enim ipsam</span><b>VOLUPTATEM QUIA VOLUPTAS</b>Good supplies support good care. Plan orders around patient volume, seasonal needs and storage space. Ask staff what runs out first, check expiry dates monthly and keep a short list of trusted backup vendors for urgent needs.</p>
    <span class="folio" style="right:12px;top:100px;transform:rotate(90deg)">05</span>
    <div class="abs" style="right:14px;top:118px;height:180px;border-left:.5px dotted #999"></div>
    <span class="side-running" style="top:300px">runningTitle</span>
  </div>
</section>

<!-- ===== Employment options ===== -->
<section class="sheet spread employment" aria-label="Employment options spread">
  <div class="page">
    <span class="folio" style="left:18px">06</span>
    <div class="folio-line" style="left:30px;width:150px"></div>
    <span class="running" style="right:10px">runningTitle</span>
    <div class="photo surgeon" role="img" aria-label="Surgeon in blue scrubs and cap putting on gloves"></div>
    <p class="body-copy" style="left:151px;top:105px;width:72px"><span class="kicker">Sed ut perspiciatis</span><b>UNDE OMNIS ISTE NATUS ONSEQUATUR</b>Employed roles offer steady pay and fewer admin tasks, while private practice gives more control over schedule and growth.</p>
    <div class="photo paper" role="img" aria-label="Doctor writing notes on a clipboard"></div>
    <h2 class="section-title" style="left:22px;top:240px">employment<span class="accent">options</span></h2>
    <div class="abs caption-box"><b>PHOTO1.</b> Nemo enim ipsam voluptatem quia voluptas minima veniam<br><b>PHOTO2.</b> Enim ad minima veniam, quis nostrum exercitationem ullam<br><b>PHOTO3.</b> Minus id quod maxime placeat facere possimus</div>
  </div>
  <div class="page right">
    <p class="body-copy" style="left:8px;top:38px;width:72px">Before choosing a role, compare benefits, call schedules and contract terms with a trusted advisor.</p>
    <p class="body-copy" style="left:8px;top:84px;width:72px"><span class="kicker">Nemo enim ipsam</span><b>VOLUPTATEM QUIA VOLUPTAS</b>Hospital groups, clinics and partnerships each bring different duties. Ask about productivity targets, support staff, malpractice cover and how bonuses are paid before you sign.</p>
    <div class="photo blocks" role="img" aria-label="Hand stacking wooden blocks printed with medical icons"></div>
    <div class="photo pink" role="img" aria-label="Stethoscope and pills on a pink background"></div>
    <p class="body-copy" style="left:88px;top:245px;width:72px">Talk with colleagues who made the same move. Their honest notes on workload, pay and family time often matter more than any offer letter.</p>
    <span class="folio" style="right:12px;top:100px;transform:rotate(90deg)">07</span>
    <div class="abs" style="right:14px;top:118px;height:180px;border-left:.5px dotted #999"></div>
    <span class="side-running" style="top:300px">runningTitle</span>
  </div>
  <div class="banner">But who has any right to find fault with a man who chooses to enjoy a pleasure that has no annoying consequences, or one who avoids a pain that produces no resultant pleasure? On the other hand, we denounce with righteous indignation</div>
</section>

</body>
</html>
```